Ledger Lanternfox Powerpoint with Marshal Valorline Type Theme

Need powerpoint template with matching colors and different slide options. Logo and colors to be used can be found at ledgerlanternfox.example. Want brightly colored slide deck that is readable form the back of a room, but highlights colors. I will be incorporating Quizzap into the slides to gamify my presentations.

Target Market(s)

Tech

Industry/Entity Type

IT, specifically database, but crossing over to mental health in IT, important note this is not for a company, this is just for a professional building a brand

Font styles to use
Sans Serif

Colors
0054AA
0677BA
7BADD7
CADEEF
E8F1F8
EB3D1F
EC4F4E
F09395
F8D3D4
FCEDEE

Requirements
Must have
• My Logo in the bottom corner, front page, a thank your page, question page, content page, content page with two columns, content page with graphs, and icons to be used in the primary colors of the logos, About Me Page, Break Slides, Demo break slide
Should not have
• Lighter shades of colors, I want to pop out where colors are used, I want spacing and font size to be readable from the back of a room, most likely black text and white background

```html
<!DOCTYPE html>
<html lang="en">
<head>
<meta charset="utf-8">
<title>Ledger Lanternfox – Slide Theme Overview</title>
<link href="https://fonts.googleapis.com/css2?family=Poppins:wght@300;400;500;600;700&family=Montserrat:wght@400;500;600;700&display=swap" rel="stylesheet">
<style>
:root{
  --blue:#1d3e78;
  --blue-deep:#173465;
  --blue-photo:#2a4f8c;
  --red:#e5262c;
  --gray:#7d7d7d;
  --ink:#3b3b3b;
  --muted:#8c8c8c;
  --line:#e6e6e6;
  --pale:#e9eef7;
  --canvas:#dcdcdc;
  --white:#ffffff;
}
*{box-sizing:border-box;margin:0;padding:0}
html,body{width:790px;height:1200px;overflow:hidden}
body{background:var(--canvas);position:relative;font-family:"Montserrat",sans-serif;color:var(--ink)}
.cell{position:absolute;width:255px;height:143px;overflow:hidden}
.slide{position:absolute;left:0;top:0;width:506px;height:284px;transform:scale(.504);transform-origin:0 0;background:var(--white);overflow:hidden}
.abs{position:absolute}
.photo{position:absolute;background:linear-gradient(135deg,#3a5f9a,#1f3d73)}
.heading{font-family:"Poppins",sans-serif;font-weight:600;color:var(--blue);line-height:1.05}
.bar{display:block;width:22px;height:4px;background:var(--red);margin-top:6px}
.bar.center{margin:6px auto 0}
.copy{font-size:5.6px;line-height:1.45;color:var(--muted)}
.brandmark{font-family:"Poppins",sans-serif;font-weight:700;white-space:nowrap}
.rail{position:absolute;left:0;top:0;bottom:0;width:30px;border-right:1px solid var(--line)}
.rail .dot{position:absolute;left:9px;top:6px;width:12px;height:12px;border-radius:50%;background:var(--blue)}
.rail .brand{position:absolute;left:9px;top:118px;writing-mode:vertical-rl;transform:rotate(180deg);font-family:"Poppins",sans-serif;font-weight:700;font-size:6px;color:var(--red)}
.rail .num{position:absolute;left:8px;bottom:6px;font-size:5px;font-weight:700;color:var(--ink)}
.pill{position:absolute;border-radius:10px;font-size:5px;letter-spacing:1.5px;color:var(--white);text-align:center}
.center{text-align:center}
.iconbubble{position:absolute;width:26px;height:26px;border-radius:50%;background:var(--white);box-shadow:0 1px 4px rgba(0,0,0,.15);display:flex;align-items:center;justify-content:center}
.name{font-size:6px;font-weight:700;color:var(--ink)}
.qa-box{position:absolute;width:22px;height:22px;border-radius:3px;color:#fff;font-family:"Poppins",sans-serif;font-weight:700;font-size:11px;display:flex;align-items:center;justify-content:center}
.qa-text{position:absolute;width:120px;font-size:5.6px;line-height:1.35;color:var(--muted)}
.table-row{position:absolute;height:22px;display:flex;align-items:center;font-size:5px}
</style>
</head>
<body>

<!-- Row 1 -->
<div class="cell" style="left:7px;top:7px">
 <div class="slide" style="background:var(--blue)">
  <div class="photo" role="img" aria-label="Blue-toned photo of a person working on a tablet" style="inset:0;background:linear-gradient(160deg,#35598f,#1d3e78 60%,#1a376c)"></div>
  <div class="abs brandmark center" style="left:0;right:0;top:52px;font-size:12px;color:#fff">Ledger Lanternfox</div>
  <div class="pill" style="left:158px;top:84px;width:176px;height:14px;line-height:14px;background:rgba(255,255,255,.2)">www.ledgerlanternfox.example</div>
  <div class="abs heading center" style="left:0;right:0;top:112px;font-size:31px;color:#fff">Presentation<br>Title Goes Here</div>
  <div class="abs center" style="left:0;right:0;top:180px;font-size:11px;color:#fff;font-family:Poppins,sans-serif;font-weight:300">Sub Title Goes Here</div>
  <div class="pill" style="left:191px;top:230px;width:108px;height:18px;line-height:18px;background:var(--red);font-weight:700;letter-spacing:0;font-size:6px">Oct 2021</div>
 </div>
</div>

<div class="cell" style="left:268px;top:7px">
 <div class="slide">
  <div class="photo" role="img" aria-label="Blue-toned photo of hands holding a tablet" style="left:0;top:0;width:506px;height:238px;background:linear-gradient(150deg,#3a5e97,#1d3e78 55%,#1a396f)"></div>
  <div class="abs heading" style="left:25px;top:92px;font-size:26px;color:#fff;font-weight:700">TITLE OF<br>PRESENTATION</div>
  <div class="abs" style="left:28px;top:180px;font-size:7px;color:#fff;line-height:1.4">Here is A place for Credentials<br>Date: 2021 March</div>
  <div class="abs" style="left:20px;top:250px;width:22px;height:22px;border-radius:50%;background:var(--blue)"></div>
  <div class="abs brandmark" style="left:48px;top:254px;font-size:11px;color:var(--red)">Ledger Lanternfox</div>
  <div class="abs" style="left:400px;top:258px;font-size:7px;font-weight:700;color:var(--blue)">Presenter Name</div>
 </div>
</div>

<div class="cell" style="left:528px;top:7px">
 <div class="slide">
  <div class="photo" role="img" aria-label="Blue-toned photo of server racks" style="inset:0;background:linear-gradient(110deg,#1d3e78 40%,#2f5590 75%,#23457f)"></div>
  <div class="abs brandmark" style="left:32px;top:78px;font-size:10px;color:var(--red)">Ledger Lanternfox</div>
  <div class="abs heading" style="left:30px;top:108px;font-size:26px;color:#fff;font-weight:700">TITLE OF<br>PRESENTATION</div>
  <div class="abs" style="left:33px;top:198px;font-size:7px;color:#fff;line-height:1.4">Here is A place for Credentials<br>Date: 2021 March</div>
 </div>
</div>

<!-- Row 2 -->
<div class="cell" style="left:7px;top:156px">
 <div class="slide" style="background:var(--blue)">
  <svg class="abs" style="left:0;top:0" width="506" height="284" role="img" aria-label="Photo of a laptop on a desk">
   <defs><linearGradient id="deskTone" x1="0" y1="0" x2="1" y2="1"><stop offset="0" stop-color="#8a8f96"/><stop offset="1" stop-color="#3f4652"/></linearGradient></defs>
   <polygon points="300,0 506,0 506,145 205,145" fill="url(#deskTone)"/>
   <polygon points="130,220 506,220 506,284 100,284" fill="#a58a6c"/>
  </svg>
  <svg class="abs" style="left:0;top:0" width="506" height="284"><polygon points="168,146 506,146 506,220 130,220" fill="var(--red)"/></svg>
  <div class="abs brandmark" style="left:50px;top:70px;font-size:24px;color:#fff">Ledger<br>Lanternfox</div>
  <div class="abs heading center" style="left:170px;top:155px;width:310px;font-size:27px;color:#fff">Presentation<br>Title Goes Here</div>
 </div>
</div>

<div class="cell" style="left:268px;top:156px">
 <div class="slide">
  <div class="abs brandmark" style="left:250px;top:110px;font-size:44px;color:var(--pale)">Ledger Lanternfox</div>
  <div class="abs brandmark" style="left:32px;top:60px;font-size:14px;color:var(--red)">Ledger Lanternfox</div>
  <div class="abs heading" style="left:31px;top:104px;font-size:32px">Presentation<br>Title Goes Here</div>
  <div class="abs" style="left:32px;top:170px;font-size:11px;color:var(--red);font-family:Poppins,sans-serif">Sub Title Goes Here</div>
  <div class="pill" style="left:27px;top:224px;width:152px;height:16px;line-height:16px;background:var(--red)">www.ledgerlanternfox.example</div>
 </div>
</div>

<div class="cell" style="left:528px;top:156px">
 <div class="slide">
  <div class="abs" style="left:0;top:0;width:506px;height:10px;background:var(--blue)"></div>
  <div class="abs" style="left:0;top:268px;width:506px;height:10px;background:var(--red)"></div>
  <div class="abs" style="left:20px;top:58px;font-family:Poppins,sans-serif;font-weight:700;font-size:64px;color:#e5e9f0;line-height:1">01</div>
  <div class="abs" style="left:48px;top:80px;font-family:Poppins,sans-serif;font-weight:300;font-size:40px;line-height:1;color:var(--blue)">Slide<br>Break</div>
  <div class="abs copy" style="left:48px;top:172px;width:212px;color:var(--blue)">Lorem ipsum dolor sit amet, consectetur adipiscing elit, sed do eiusmod tempor incididunt ut labore et dolore magna aliqua. Lorem ipsum dolor sit amet, consectetur adipiscing elit, sed do eiusmod tempor incididunt ut labore et dolore magna aliqua.</div>
  <div class="abs" style="left:318px;top:105px;width:28px;height:28px;border-radius:50%;background:var(--blue)"></div>
  <div class="abs brandmark" style="left:352px;top:110px;font-size:15px;color:var(--blue)">Ledger Lanternfox</div>
 </div>
</div>

<!-- Row 3 -->
<div class="cell" style="left:7px;top:305px">
 <div class="slide">
  <div class="rail"><span class="dot"></span><span class="brand">Ledger Lanternfox</span><span class="num">7</span></div>
  <div class="abs heading" style="left:45px;top:28px;font-size:21px">Title And Body Slide<span class="bar"></span></div>
  <div class="abs brandmark" style="left:225px;top:120px;font-size:30px;color:var(--pale)">Ledger Lanternfox</div>
 </div>
</div>

<div class="cell" style="left:268px;top:305px">
 <div class="slide">
  <div class="rail"><span class="dot"></span><span class="brand">Ledger Lanternfox</span><span class="num">8</span></div>
  <div class="abs heading" style="left:45px;top:28px;font-size:21px">Title And Body Slide<span class="bar"></span></div>
  <div class="abs copy" style="left:50px;top:88px;width:422px;text-align:justify;font-size:5.4px">
   <p style="margin-bottom:7px">Lorem ipsum dolor sit amet, consectetur adipiscing elit, sed do eiusmod tempor incididunt ut labore et dolore magna aliqua. Lorem ipsum dolor sit amet, consectetur adipiscing elit, sed do eiusmod tempor incididunt ut labore et dolore magna aliqua. Ut enim ad minim veniam, quis nostrud exercitation ullamco laboris nisi ut aliquip.</p>
   <p style="margin-bottom:7px">Lorem ipsum dolor sit amet, consectetur adipiscing elit. Lorem ipsum dolor sit amet, consectetur adipiscing elit, sed do eiusmod tempor incididunt ut labore et dolore magna aliqua. Lorem ipsum dolor sit amet, consectetur adipiscing elit, sed do eiusmod tempor incididunt ut labore et dolore magna aliqua. Ut enim ad minim veniam, quis nostrud exercitation ullamco laboris nisi ut aliquip.</p>
   <p>Lorem ipsum dolor sit amet, consectetur adipiscing elit, sed do eiusmod tempor incididunt ut labore et dolore magna aliqua. Lorem ipsum dolor sit amet, consectetur adipiscing elit, sed do eiusmod tempor incididunt ut labore et dolore magna aliqua. Sed do eiusmod tempor incididunt ut labore et dolore magna aliqua. Lorem ipsum dolor sit amet, consectetur adipiscing elit, sed do eiusmod tempor incididunt ut labore et dolore magna aliqua. Ut enim ad minim veniam, quis nostrud exercitation ullamco laboris nisi ut aliquip.</p>
  </div>
 </div>
</div>

<div class="cell" style="left:528px;top:305px">
 <div class="slide">
  <div class="rail"><span class="dot"></span><span class="brand">Ledger Lanternfox</span><span class="num">9</span></div>
  <div class="abs heading" style="left:50px;top:80px;font-size:27px">Pic And Text<span class="bar"></span></div>
  <div class="abs copy" style="left:50px;top:138px;width:172px;text-align:justify;font-size:6.2px;color:var(--ink)">Lorem ipsum dolor sit amet, consectetur adipiscing elit, sed do eiusmod tempor incididunt ut labore et dolore magna aliqua. Lorem ipsum dolor sit amet, consectetur adipiscing elit, sed do eiusmod tempor incididunt ut labore et dolore magna aliqua. Ut enim ad minim veniam, quis nostrud exercitation ullamco laboris nisi ut aliquip.</div>
  <div class="abs" style="left:248px;top:37px;width:167px;height:157px;background:var(--red)"></div>
  <div class="photo" role="img" aria-label="Photo of a person typing at a desktop computer" style="left:274px;top:65px;width:210px;height:182px;background:linear-gradient(135deg,#4b4f58,#b9b1a5);box-shadow:0 4px 12px rgba(0,0,0,.25)"></div>
 </div>
</div>

<!-- Row 4 -->
<div class="cell" style="left:7px;top:454px">
 <div class="slide">
  <div class="photo" role="img" aria-label="Photo of a hiker standing on a mountain peak" style="left:0;top:0;width:218px;height:284px;background:linear-gradient(180deg,#2c4b52,#6f8384 45%,#3a3f3f)"></div>
  <div class="abs" style="left:249px;top:80px;width:56px;height:2px;background:var(--red)"></div>
  <div class="abs heading" style="left:249px;top:88px;width:215px;font-size:11.5px;font-weight:500;line-height:1.3">Success is not only what you achieve in your life, but also what you inspire in the lives of others</div>
  <div class="abs" style="left:113px;top:186px;width:393px;height:98px;background:var(--blue)"></div>
  <div class="abs" style="left:147px;top:214px;width:100px;color:#fff"><div style="font-size:7px;font-weight:700;margin-bottom:6px">Lorem ipsum dolor</div><div style="font-size:5px;line-height:1.5">Lorem ipsum dolor sit amet, consectetur adipiscing elit, sed do eiusmod tempor</div></div>
  <div class="abs" style="left:267px;top:212px;width:100px;color:#fff"><div style="font-size:7px;font-weight:700;margin-bottom:6px">Lorem ipsum dolor</div><div style="font-size:5px;line-height:1.5">Lorem ipsum dolor sit amet, consectetur adipiscing elit, sed do eiusmod tempor</div></div>
  <div class="abs" style="left:391px;top:212px;width:100px;color:#fff"><div style="font-size:7px;font-weight:700;margin-bottom:6px">Lorem ipsum dolor</div><div style="font-size:5px;line-height:1.5">Lorem ipsum dolor sit amet, consectetur adipiscing elit, sed do eiusmod tempor</div></div>
 </div>
</div>

<div class="cell" style="left:268px;top:454px">
 <div class="slide">
  <div class="rail"><span class="dot"></span><span class="brand">Ledger Lanternfox</span><span class="num">11</span></div>
  <div class="abs" style="left:31px;top:0;width:475px;height:143px;background:var(--blue)"></div>
  <div class="abs heading center" style="left:31px;right:0;top:40px;font-size:21px;color:#fff">Here Add Awesome Text<span class="bar center"></span></div>
  <svg class="abs" style="left:0;top:0" width="506" height="284">
   <g fill="var(--red)" stroke="#fff" stroke-width="2.5">
    <circle cx="118" cy="137" r="27"/><circle cx="258" cy="137" r="27"/><circle cx="400" cy="137" r="27"/>
   </g>
   <g fill="none" stroke="#fff" stroke-width="1.6">
    <circle cx="118" cy="137" r="10"/><circle cx="118" cy="137" r="5"/><line x1="118" y1="137" x2="132" y2="123"/>
    <path d="M250 146 L266 128 M266 128 l-6 0 M266 128 l0 6 M250 146 l-4 4"/>
    <path d="M390 148 h20 M393 148 v-8 M399 148 v-13 M405 148 v-18"/>
   </g>
  </svg>
  <div class="abs center" style="left:53px;top:172px;width:130px"><div class="name" style="font-size:8px;margin-bottom:7px">Project name</div><div class="copy">Lorem ipsum dolor sit amet, nec an dictas equidem appellantur, ut has commune accommodare. Mea illum, ludus solet idpro.</div></div>
  <div class="abs center" style="left:193px;top:172px;width:130px"><div class="name" style="font-size:8px;margin-bottom:7px">Project name</div><div class="copy">Lorem ipsum dolor sit amet, nec an dictas equidem appellantur, ut has commune accommodare. Mea illum, ludus solet idpro.</div></div>
  <div class="abs center" style="left:335px;top:172px;width:130px"><div class="name" style="font-size:8px;margin-bottom:7px">Project name</div><div class="copy">Lorem ipsum dolor sit amet, nec an dictas equidem appellantur, ut has commune accommodare. Mea illum, ludus solet idpro.</div></div>
 </div>
</div>

<div class="cell" style="left:528px;top:454px">
 <div class="slide">
  <div class="rail"><span class="dot"></span><span class="brand">Ledger Lanternfox</span><span class="num">12</span></div>
  <div class="abs heading center" style="left:31px;right:0;top:32px;font-size:21px">3 Columns Slide<span class="bar center"></span></div>
  <div class="abs" style="left:69px;top:118px;width:115px;height:100px;background:var(--red);border-radius:4px"></div>
  <div class="abs" style="left:197px;top:118px;width:115px;height:100px;background:var(--blue);border-radius:4px"></div>
  <div class="abs" style="left:327px;top:118px;width:115px;height:100px;background:var(--gray);border-radius:4px"></div>
  <div class="iconbubble" style="left:113px;top:103px;width:28px;height:28px"><svg width="14" height="14"><circle cx="7" cy="7" r="3" fill="none" stroke="var(--red)"/><circle cx="2" cy="2" r="1.5" fill="var(--red)"/><circle cx="12" cy="2" r="1.5" fill="var(--red)"/><circle cx="2" cy="12" r="1.5" fill="var(--red)"/><circle cx="12" cy="12" r="1.5" fill="var(--red)"/></svg></div>
  <div class="iconbubble" style="left:241px;top:103px;width:28px;height:28px"><svg width="14" height="14"><circle cx="7" cy="7" r="6" fill="none" stroke="var(--blue)"/><circle cx="7" cy="7" r="3" fill="none" stroke="var(--blue)"/></svg></div>
  <div class="iconbubble" style="left:371px;top:103px;width:28px;height:28px"><svg width="14" height="14"><circle cx="7" cy="7" r="6" fill="none" stroke="var(--gray)"/><circle cx="7" cy="5" r="2" fill="var(--gray)"/><path d="M3 11 q4 -5 8 0" fill="none" stroke="var(--gray)"/></svg></div>
  <div class="abs center" style="left:74px;top:146px;width:105px;color:#fff"><div style="font-size:6px;font-weight:700;margin-bottom:4px">Project name here</div><div style="font-size:5.2px;line-height:1.35">Lorem ipsum dolor sit amet, nec an dictas equidem appellantur, ut has commune accommodare. Mea illum, ludus solet idpro.</div></div>
  <div class="abs center" style="left:202px;top:146px;width:105px;color:#fff"><div style="font-size:6px;font-weight:700;margin-bottom:4px">Project name here</div><div style="font-size:5.2px;line-height:1.35">Lorem ipsum dolor sit amet, nec an dictas equidem appellantur, ut has commune accommodare. Mea illum, ludus solet idpro.</div></div>
  <div class="abs center" style="left:332px;top:146px;width:105px;color:#fff"><div style="font-size:6px;font-weight:700;margin-bottom:4px">Project name here</div><div style="font-size:5.2px;line-height:1.35">Lorem ipsum dolor sit amet, nec an dictas equidem appellantur, ut has commune accommodare. Mea illum, ludus solet idpro.</div></div>
 </div>
</div>

<!-- Row 5 -->
<div class="cell" style="left:7px;top:603px">
 <div class="slide">
  <div class="rail"><span class="dot"></span><span class="brand">Ledger Lanternfox</span><span class="num">13</span></div>
  <svg class="abs" style="left:0;top:0" width="506" height="284"><polygon points="31,0 208,0 375,284 31,284" fill="var(--blue)"/></svg>
  <div class="abs heading" style="left:56px;top:88px;font-size:21px;color:#fff">A Place for<br>Screenshot<span class="bar"></span></div>
  <div class="abs" style="left:56px;top:155px;width:150px;font-size:5.6px;line-height:1.45;color:#fff">Lorem ipsum dolor sit amet, consectetur adipiscing elit, sed do eiusmod tempor ela beta on lipon eterim dolor sin ter ti.</div>
  <div class="abs" style="left:228px;top:62px;width:272px;height:180px;background:#222;border-radius:8px"></div>
  <div class="abs" style="left:236px;top:70px;width:256px;height:162px;background:#a3a3a3;display:flex;align-items:center;justify-content:center;font-size:9px;font-weight:600;color:#fff">HERE YOU CAN ADD A SCREENSHOT</div>
  <div class="abs" style="left:198px;top:240px;width:308px;height:8px;background:linear-gradient(#d8d8d8,#9a9a9a);border-radius:0 0 6px 6px"></div>
 </div>
</div>

<div class="cell" style="left:268px;top:603px">
 <div class="slide">
  <div class="rail"><span class="dot"></span><span class="brand">Ledger Lanternfox</span><span class="num">14</span></div>
  <div class="abs heading center" style="left:31px;right:0;top:22px;font-size:21px">6 Columns Slide<span class="bar center"></span></div>
  <div class="abs" style="left:48px;top:90px;width:420px;display:grid;grid-template-columns:1fr 1fr;row-gap:18px;column-gap:12px">
   <div style="display:flex;gap:8px"><div class="iconbubble" style="position:static;flex:none;width:24px;height:24px"><svg width="10" height="12"><rect x="1" y="1" width="8" height="10" fill="none" stroke="var(--blue)"/><line x1="3" y1="4" x2="7" y2="4" stroke="var(--red)"/><line x1="3" y1="7" x2="7" y2="7" stroke="var(--blue)"/></svg></div><div><div class="name">Project name</div><div class="copy" style="font-size:5.2px;line-height:1.3">Lorem ipsum dolor sit amet, nec an dictas equidem appellantur, ut has commune accommodare. Mea illum, ludus solet idpro.</div></div></div>
   <div style="display:flex;gap:8px"><div class="iconbubble" style="position:static;flex:none;width:24px;height:24px"><svg width="10" height="12"><rect x="1" y="1" width="8" height="10" fill="none" stroke="var(--blue)"/><line x1="3" y1="4" x2="7" y2="4" stroke="var(--red)"/><line x1="3" y1="7" x2="7" y2="7" stroke="var(--blue)"/></svg></div><div><div class="name">Project name</div><div class="copy" style="font-size:5.2px;line-height:1.3">Lorem ipsum dolor sit amet, nec an dictas equidem appellantur, ut has commune accommodare. Mea illum, ludus solet idpro.</div></div></div>
   <div style="display:flex;gap:8px"><div class="iconbubble" style="position:static;flex:none;width:24px;height:24px"><svg width="12" height="12"><path d="M1 11 h10 M3 11 v-3 M6 11 v-5 M9 11 v-8" stroke="var(--blue)" fill="none"/></svg></div><div><div class="name">Project name</div><div class="copy" style="font-size:5.2px;line-height:1.3">Lorem ipsum dolor sit amet, nec an dictas equidem appellantur, ut has commune accommodare. Mea illum, ludus solet idpro.</div></div></div>
   <div style="display:flex;gap:8px"><div class="iconbubble" style="position:static;flex:none;width:24px;height:24px"><svg width="12" height="12"><path d="M1 11 h10 M3 11 v-3 M6 11 v-5 M9 11 v-8" stroke="var(--blue)" fill="none"/></svg></div><div><div class="name">Project name</div><div class="copy" style="font-size:5.2px;line-height:1.3">Lorem ipsum dolor sit amet, nec an dictas equidem appellantur, ut has commune accommodare. Mea illum, ludus solet idpro.</div></div></div>
   <div style="display:flex;gap:8px"><div class="iconbubble" style="position:static;flex:none;width:24px;height:24px"><svg width="12" height="12"><path d="M1 11 h10 M3 11 v-4 M6 11 v-6 M9 11 v-3" stroke="var(--red)" fill="none"/></svg></div><div><div class="name">Project name</div><div class="copy" style="font-size:5.2px;line-height:1.3">Lorem ipsum dolor sit amet, nec an dictas equidem appellantur, ut has commune accommodare. Mea illum, ludus solet idpro.</div></div></div>
   <div style="display:flex;gap:8px"><div class="iconbubble" style="position:static;flex:none;width:24px;height:24px"><svg width="12" height="12"><path d="M1 11 h10 M3 11 v-4 M6 11 v-6 M9 11 v-3" stroke="var(--red)" fill="none"/></svg></div><div><div class="name">Project name</div><div class="copy" style="font-size:5.2px;line-height:1.3">Lorem ipsum dolor sit amet, nec an dictas equidem appellantur, ut has commune accommodare. Mea illum, ludus solet idpro.</div></div></div>
  </div>
 </div>
</div>

<div class="cell" style="left:528px;top:603px">
 <div class="slide">
  <div class="rail"><span class="dot"></span><span class="brand">Ledger Lanternfox</span><span class="num">15</span></div>
  <div class="abs heading center" style="left:31px;right:0;top:22px;font-size:21px">Chart Slide<span class="bar center"></span></div>
  <div class="table-row" style="left:163px;top:67px;width:308px;background:var(--red);color:#fff;font-weight:600;justify-content:space-around"><span>Your Text Here</span><span>Your Text Here</span><span>Your Text Here</span><span>Your Text Here</span></div>
  <svg class="abs" style="left:40px;top:91px" width="431" height="154">
   <rect x="0" y="0" width="123" height="154" fill="var(--blue)"/>
   <g stroke="#eaeaea"><line x1="123" y1="22" x2="431" y2="22"/><line x1="123" y1="44" x2="431" y2="44"/><line x1="123" y1="66" x2="431" y2="66"/><line x1="123" y1="88" x2="431" y2="88"/><line x1="123" y1="110" x2="431" y2="110"/><line x1="123" y1="132" x2="431" y2="132"/><line x1="0" y1="22" x2="123" y2="22" stroke="#2f5290"/><line x1="0" y1="44" x2="123" y2="44" stroke="#2f5290"/><line x1="0" y1="66" x2="123" y2="66" stroke="#2f5290"/><line x1="0" y1="88" x2="123" y2="88" stroke="#2f5290"/><line x1="0" y1="110" x2="123" y2="110" stroke="#2f5290"/><line x1="0" y1="132" x2="123" y2="132" stroke="#2f5290"/></g>
   <g font-family="Montserrat,sans-serif" font-size="5.5" font-weight="600" fill="#fff" text-anchor="middle">
    <text x="61" y="13">You can replace this text</text><text x="61" y="35">You can replace this text</text><text x="61" y="57">You can replace this text</text><text x="61" y="79">You can replace this text</text><text x="61" y="101">You can replace this text</text><text x="61" y="123">You can replace this text</text><text x="61" y="145">You can replace this text</text>
   </g>
   <g font-family="Montserrat,sans-serif" font-size="5" fill="#8c8c8c" text-anchor="middle">
    <text x="160" y="13">1250</text><text x="160" y="35">3623</text><text x="160" y="57">2589</text><text x="160" y="79">1020</text><text x="160" y="101">2320</text><text x="160" y="123">5698</text><text x="160" y="145">1999</text>
    <text x="315" y="13">50%</text><text x="315" y="35">50%</text><text x="315" y="57">12%</text><text x="315" y="79">65%</text><text x="315" y="101">36%</text><text x="315" y="123">95%</text><text x="315" y="145">66%</text>
    <text x="393" y="13">1250</text><text x="393" y="35">3623</text><text x="393" y="57">2589</text><text x="393" y="79">1020</text><text x="393" y="101">2320</text><text x="393" y="123">5698</text><text x="393" y="145">1999</text>
   </g>
   <g stroke="var(--blue)" stroke-width="2" fill="none" stroke-linecap="round">
    <path d="M234 9 l3 3 l6 -6"/><path d="M234 53 l3 3 l6 -6"/><path d="M234 97 l3 3 l6 -6"/>
    <path d="M235 30 l6 6 M241 30 l-6 6"/><path d="M235 74 l6 6 M241 74 l-6 6"/><path d="M235 118 l6 6 M241 118 l-6 6"/><path d="M235 140 l6 6 M241 140 l-6 6"/>
   </g>
  </svg>
 </div>
</div>

<!-- Row 6 -->
<div class="cell" style="left:7px;top:752px">
 <div class="slide">
  <div class="rail"><span class="dot"></span><span class="brand">Ledger Lanternfox</span><span class="num">16</span></div>
  <div class="abs heading" style="left:44px;top:28px;font-size:21px">Smart Art Slide<span class="bar"></span></div>
  <div class="abs" style="left:45px;top:90px;width:175px;display:flex;flex-direction:column;gap:18px">
   <div style="display:flex;gap:8px"><div class="iconbubble" style="position:static;flex:none;width:24px;height:24px"><svg width="12" height="12"><circle cx="6" cy="6" r="5" fill="none" stroke="var(--blue)"/><circle cx="6" cy="6" r="2" fill="var(--red)"/></svg></div><div><div class="name">Lorem ipsum dolor</div><div class="copy" style="font-size:5px;line-height:1.3">Lorem ipsum dolor sit amet, consectetur adipiscing elit, sed do eiusmod tempor ela beta on lipon eterim dolor sin ter ti.</div></div></div>
   <div style="display:flex;gap:8px"><div class="iconbubble" style="position:static;flex:none;width:24px;height:24px"><svg width="12" height="12"><path d="M2 10 L10 2 M10 2 h-4 M10 2 v4" stroke="var(--blue)" fill="none"/></svg></div><div><div class="name">Lorem ipsum dolor</div><div class="copy" style="font-size:5px;line-height:1.3">Lorem ipsum dolor sit amet, consectetur adipiscing elit, sed do eiusmod tempor ela beta on lipon eterim dolor sin ter ti.</div></div></div>
   <div style="display:flex;gap:8px"><div class="iconbubble" style="position:static;flex:none;width:24px;height:24px"><svg width="12" height="12"><rect x="2" y="1" width="8" height="10" fill="none" stroke="var(--blue)"/><circle cx="6" cy="7" r="2" fill="none" stroke="var(--red)"/></svg></div><div><div class="name">Lorem ipsum dolor</div><div class="copy" style="font-size:5px;line-height:1.3">Lorem ipsum dolor sit amet, consectetur adipiscing elit, sed do eiusmod tempor ela beta on lipon eterim dolor sin ter ti.</div></div></div>
  </div>
  <svg class="abs" style="left:0;top:0" width="506" height="284" stroke-linejoin="round">
   <polygon points="374,72 428,155 320,155" fill="var(--blue)" stroke="var(--blue)" stroke-width="6"/>
   <polygon points="317,163 370,163 370,250 272,250" fill="var(--red)" stroke="var(--red)" stroke-width="6"/>
   <polygon points="379,163 431,163 476,250 379,250" fill="var(--gray)" stroke="var(--gray)" stroke-width="6"/>
   <g font-family="Montserrat,sans-serif" fill="#fff" text-anchor="middle">
    <text x="374" y="112" font-size="6" font-weight="700">Project</text><text x="374" y="120" font-size="6" font-weight="700">name</text>
    <text x="374" y="129" font-size="4.2">Lorem ipsum dolor sit</text><text x="374" y="135" font-size="4.2">amet, nec an dictas</text><text x="374" y="141" font-size="4.2">equidem appellantur</text>
   </g>
   <g font-family="Montserrat,sans-serif" fill="#fff">
    <text x="308" y="208" font-size="6" font-weight="700">Project name</text><text x="296" y="217" font-size="4.2">Lorem ipsum dolor sit</text><text x="294" y="223" font-size="4.2">amet, nec an dictas</text><text x="292" y="229" font-size="4.2">equidem appellantur</text>
    <text x="392" y="208" font-size="6" font-weight="700">Project name</text><text x="392" y="217" font-size="4.2">Lorem ipsum dolor sit</text><text x="392" y="223" font-size="4.2">amet, nec an dictas</text><text x="392" y="229" font-size="4.2">equidem appellantur</text>
   </g>
  </svg>
 </div>
</div>

<div class="cell" style="left:268px;top:752px">
 <div class="slide">
  <div class="rail"><span class="dot"></span><span class="brand">Ledger Lanternfox</span><span class="num">17</span></div>
  <div class="abs heading center" style="left:31px;right:0;top:22px;font-size:21px">Here is Quotes<span class="bar center"></span></div>
  <div class="abs" style="left:50px;top:80px;width:185px">
   <div style="font-family:Poppins,sans-serif;font-weight:700;font-size:34px;line-height:.7;color:var(--red);height:22px">&#8221;</div>
   <div style="font-size:8px;line-height:1.75;color:var(--ink);margin-top:4px">Lorem ipsum dolor sit amet, consectetur adipiscing elit, sed do eiusmod tempor incididunt ut labore et dolore magna aliqua. Lorem ipsum dolor sit amet, consectetur adipiscing elit.</div>
   <div style="display:flex;align-items:center;gap:8px;margin-top:14px"><span style="width:24px;height:24px;border-radius:50%;background:#d5d5d5"></span><div><div style="font-size:7px;font-weight:600;color:var(--blue)">Your Name</div><div style="font-size:6px;color:var(--muted)">Founder</div></div></div>
  </div>
  <div class="abs" style="left:283px;top:80px;width:185px">
   <div style="font-family:Poppins,sans-serif;font-weight:700;font-size:34px;line-height:.7;color:var(--blue);height:22px">&#8221;</div>
   <div style="font-size:8px;line-height:1.75;color:var(--ink);margin-top:4px">Lorem ipsum dolor sit amet, consectetur adipiscing elit, sed do eiusmod tempor incididunt ut labore et dolore magna aliqua. Lorem ipsum dolor sit amet, consectetur adipiscing elit.</div>
   <div style="display:flex;align-items:center;gap:8px;margin-top:14px"><span style="width:24px;height:24px;border-radius:50%;background:#d5d5d5"></span><div><div style="font-size:7px;font-weight:600;color:var(--blue)">Your Name</div><div style="font-size:6px;color:var(--muted)">Founder</div></div></div>
  </div>
 </div>
</div>

<div class="cell" style="left:528px;top:752px">
 <div class="slide">
  <div class="rail"><span class="dot"></span><span class="brand">Ledger Lanternfox</span><span class="num">18</span></div>
  <div class="abs heading center" style="left:31px;right:0;top:28px;font-size:21px">Here Is Statistics<span class="bar center"></span></div>
  <svg class="abs" style="left:0;top:0" width="506" height="284">
   <circle cx="116" cy="176" r="74" fill="var(--blue)"/>
   <circle cx="116" cy="196" r="52" fill="var(--red)"/>
   <circle cx="116" cy="220" r="28" fill="var(--gray)"/>
   <g stroke="#555" stroke-width=".8"><line x1="128" y1="118" x2="205" y2="120"/><line x1="130" y1="166" x2="205" y2="165"/><line x1="130" y1="218" x2="205" y2="218"/></g>
   <g font-family="Poppins,sans-serif" font-weight="700" fill="#fff" font-size="16" text-anchor="middle"><text x="116" y="127">$</text><text x="116" y="173">$</text><text x="116" y="226" font-size="13">$</text></g>
   <g font-family="Poppins,sans-serif" font-weight="600" fill="var(--blue)" font-size="12"><text x="212" y="124">5M</text><text x="212" y="169">2M</text><text x="212" y="222">1M</text></g>
   <rect x="292" y="118" width="16" height="16" fill="var(--blue)"/><path d="M296 126 l3 3 l6 -6" stroke="#fff" stroke-width="1.6" fill="none"/>
   <rect x="292" y="163" width="16" height="16" fill="var(--red)"/><path d="M296 171 l3 3 l6 -6" stroke="#fff" stroke-width="1.6" fill="none"/>
   <rect x="292" y="208" width="16" height="16" fill="#555"/><path d="M296 216 l3 3 l6 -6" stroke="#fff" stroke-width="1.6" fill="none"/>
  </svg>
  <div class="abs" style="left:319px;top:110px;width:150px"><div style="font-size:8px;font-weight:700;color:var(--blue)">Lorem ipsum dolor</div><div class="copy">Lorem ipsum dolor sit amet, consectetur adipiscing elit, sed do eiusmod tempor</div></div>
  <div class="abs" style="left:319px;top:155px;width:150px"><div style="font-size:8px;font-weight:700;color:var(--blue)">Lorem ipsum dolor</div><div class="copy">Lorem ipsum dolor sit amet, consectetur adipiscing elit, sed do eiusmod tempor</div></div>
  <div class="abs" style="left:319px;top:200px;width:150px"><div style="font-size:8px;font-weight:700;color:var(--blue)">Lorem ipsum dolor</div><div class="copy">Lorem ipsum dolor sit amet, consectetur adipiscing elit, sed do eiusmod tempor</div></div>
 </div>
</div>

<!-- Row 7 -->
<div class="cell" style="left:7px;top:901px">
 <div class="slide">
  <div class="rail"><span class="dot"></span><span class="brand">Ledger Lanternfox</span><span class="num">19</span></div>
  <div class="abs heading center" style="left:31px;right:0;top:28px;font-size:21px">Here Add Your Title<span class="bar center"></span></div>
  <div class="abs copy center" style="left:95px;top:78px;width:330px;font-size:6px">Lorem Ipsum the printing and typesetting industry. Lorem Ipsum has been the industry's standard dummy text ever since the 1500s, when an unknown printer took a galley of type and scrambled it to make a type specimen book. It has survived not only five centuries.</div>
  <svg class="abs" style="left:0;top:0" width="506" height="284" fill="none" stroke-width="5">
   <circle cx="142" cy="168" r="33" stroke="#eeeeee"/><circle cx="142" cy="168" r="33" stroke="var(--red)" stroke-dasharray="103.7 207.4" transform="rotate(-90 142 168)"/>
   <circle cx="250" cy="168" r="33" stroke="#eeeeee"/><circle cx="250" cy="168" r="33" stroke="var(--red)" stroke-dasharray="155.5 207.4" transform="rotate(-90 250 168)"/>
   <circle cx="355" cy="168" r="33" stroke="#eeeeee"/><circle cx="355" cy="168" r="33" stroke="var(--red)" stroke-dasharray="83 207.4" transform="rotate(-90 355 168)"/>
   <g font-family="Poppins,sans-serif" font-weight="600" font-size="15" fill="var(--blue)" stroke="none" text-anchor="middle"><text x="142" y="174">50%</text><text x="250" y="174">75%</text><text x="355" y="174">40%</text></g>
  </svg>
  <div class="abs copy center" style="left:102px;top:218px;width:80px">Lorem ipsum dolor amet amet consectetur dolor</div>
  <div class="abs copy center" style="left:210px;top:218px;width:80px">Lorem ipsum dolor amet amet consectetur dolor</div>
  <div class="abs copy center" style="left:315px;top:218px;width:80px">Lorem ipsum dolor amet amet consectetur dolor</div>
 </div>
</div>

<div class="cell" style="left:268px;top:901px">
 <div class="slide">
  <div class="rail"><span class="dot"></span><span class="brand">Ledger Lanternfox</span><span class="num">20</span></div>
  <div class="abs heading center" style="left:31px;right:0;top:18px;font-size:21px">Here is Statistics<span class="bar center"></span></div>
  <div class="abs center" style="left:37px;top:87px;width:121px;height:72px;background:var(--blue);color:#fff;padding-top:16px"><div style="font-size:19px;font-family:Poppins,sans-serif;font-weight:300">$0.5M</div><div style="font-size:6px">Revenue</div></div>
  <div class="abs center" style="left:37px;top:159px;width:121px;height:72px;background:#fff;box-shadow:0 2px 8px rgba(0,0,0,.12);color:var(--red);padding-top:16px"><div style="font-size:19px;font-family:Poppins,sans-serif;font-weight:300">-0.28%</div><div style="font-size:6px">Revenue</div></div>
  <svg class="abs" style="left:0;top:0" width="506" height="284">
   <g stroke="#eeeeee"><line x1="210" y1="98" x2="476" y2="98"/><line x1="210" y1="117" x2="476" y2="117"/><line x1="210" y1="136" x2="476" y2="136"/><line x1="210" y1="155" x2="476" y2="155"/><line x1="210" y1="174" x2="476" y2="174"/><line x1="210" y1="193" x2="476" y2="193"/><line x1="210" y1="212" x2="476" y2="212"/><line x1="210" y1="231" x2="476" y2="231" stroke="#ccc"/></g>
   <g font-family="Montserrat,sans-serif" font-size="4.5" fill="#777" text-anchor="end"><text x="204" y="100">$350,000</text><text x="204" y="119">$300,000</text><text x="204" y="138">$250,000</text><text x="204" y="157">$200,000</text><text x="204" y="176">$150,000</text><text x="204" y="195">$100,000</text><text x="204" y="214">$50,000</text><text x="204" y="233">$-</text></g>
   <g font-family="Montserrat,sans-serif" font-size="4.5" fill="#777" text-anchor="middle"><text x="220" y="242">Jan</text><text x="241" y="242">Feb</text><text x="262" y="242">Mar</text><text x="283" y="242">Apr</text><text x="304" y="242">May</text><text x="325" y="242">Jun</text><text x="346" y="242">Jul</text><text x="367" y="242">Aug</text><text x="388" y="242">Sep</text><text x="409" y="242">Oct</text><text x="430" y="242">Nov</text><text x="451" y="242">Dec</text><text x="472" y="242">Jan</text></g>
   <path d="M220 228 C235 222 245 222 255 215 C262 205 266 176 274 180 C282 186 286 196 292 176 C298 158 304 196 312 192 C318 186 320 168 326 174 C334 182 338 166 346 186 C352 204 356 170 364 180 C372 196 378 160 386 168 C394 178 398 190 406 186 C414 180 418 196 424 206 C430 196 438 150 448 138 C458 126 464 110 472 100" fill="none" stroke="var(--red)" stroke-width="1.2"/>
  </svg>
 </div>
</div>

<div class="cell" style="left:528px;top:901px">
 <div class="slide">
  <div class="rail"><span class="dot"></span><span class="brand">Ledger Lanternfox</span><span class="num">21</span></div>
  <div class="abs heading center" style="left:31px;right:0;top:26px;font-size:21px">Company Timeline<span class="bar center"></span></div>
  <svg class="abs" style="left:0;top:0" width="506" height="284">
   <g>
    <polygon points="48,95 124,95 142,115 124,135 48,135 62,115" fill="var(--red)"/>
    <polygon points="128,95 206,95 224,115 206,135 128,135 146,115" fill="var(--blue)"/>
    <polygon points="210,95 288,95 306,115 288,135 210,135 228,115" fill="var(--red)"/>
    <polygon points="292,95 370,95 388,115 370,135 292,135 310,115" fill="var(--blue)"/>
    <polygon points="374,95 448,95 466,115 448,135 374,135 392,115" fill="var(--red)"/>
   </g>
   <g font-family="Poppins,sans-serif" font-weight="600" font-size="8.5" fill="#fff" text-anchor="middle"><text x="100" y="118">STEP 01</text><text x="180" y="118">STEP 02</text><text x="262" y="118">STEP 03</text><text x="344" y="118">STEP 04</text><text x="424" y="118">STEP 05</text></g>
   <line x1="48" y1="146" x2="466" y2="146" stroke="#ccc"/>
   <g stroke="#bbb"><line x1="87" y1="146" x2="87" y2="170"/><line x1="170" y1="146" x2="170" y2="170"/><line x1="252" y1="146" x2="252" y2="170"/><line x1="335" y1="146" x2="335" y2="170"/><line x1="417" y1="146" x2="417" y2="170"/></g>
   <g fill="#fff" stroke="#bbb"><circle cx="87" cy="172" r="2.5"/><circle cx="170" cy="172" r="2.5"/><circle cx="252" cy="172" r="2.5"/><circle cx="335" cy="172" r="2.5"/><circle cx="417" cy="172" r="2.5"/></g>
  </svg>
  <div class="abs" style="left:50px;top:186px;width:420px;display:flex;justify-content:space-between">
   <div class="center" style="width:72px"><div class="name" style="font-size:7px;margin-bottom:5px;font-weight:600">Project name</div><div class="copy" style="font-size:5px;line-height:1.3">Lorem Ipsum is simply dummy unknown printer took a galley of type and scrambled it to make.</div></div>
   <div class="center" style="width:72px"><div class="name" style="font-size:7px;margin-bottom:5px;font-weight:600">Project name</div><div class="copy" style="font-size:5px;line-height:1.3">Lorem Ipsum is simply dummy unknown printer took a galley of type and scrambled it to make.</div></div>
   <div class="center" style="width:72px"><div class="name" style="font-size:7px;margin-bottom:5px;font-weight:600">Project name</div><div class="copy" style="font-size:5px;line-height:1.3">Lorem Ipsum is simply dummy unknown printer took a galley of type and scrambled it to make.</div></div>
   <div class="center" style="width:72px"><div class="name" style="font-size:7px;margin-bottom:5px;font-weight:600">Project name</div><div class="copy" style="font-size:5px;line-height:1.3">Lorem Ipsum is simply dummy unknown printer took a galley of type and scrambled it to make.</div></div>
   <div class="center" style="width:72px"><div class="name" style="font-size:7px;margin-bottom:5px;font-weight:600">Project name</div><div class="copy" style="font-size:5px;line-height:1.3">Lorem Ipsum is simply dummy unknown printer took a galley of type and scrambled it to make.</div></div>
  </div>
 </div>
</div>

<!-- Row 8 -->
<div class="cell" style="left:7px;top:1049px">
 <div class="slide">
  <div class="rail"><span class="dot"></span><span class="brand">Ledger Lanternfox</span><span class="num">22</span></div>
  <div class="abs heading center" style="left:31px;right:0;top:28px;font-size:21px">Q&amp;A Slide<span class="bar center"></span></div>
  <div class="qa-box" style="left:68px;top:87px;background:var(--blue)">Q</div><div class="qa-text" style="left:100px;top:88px">Lorem Ipsum is simply dummy unknown printer took a galley of type and scrambled it to make.</div>
  <div class="qa-box" style="left:68px;top:128px;background:var(--blue)">Q</div><div class="qa-text" style="left:100px;top:129px">Lorem Ipsum is simply dummy unknown printer took a galley of type and scrambled it to make.</div>
  <div class="qa-box" style="left:68px;top:169px;background:var(--blue)">Q</div><div class="qa-text" style="left:100px;top:170px">Lorem Ipsum is simply dummy unknown printer took a galley of type and scrambled it to make.</div>
  <div class="qa-box" style="left:68px;top:210px;background:var(--blue)">Q</div><div class="qa-text" style="left:100px;top:211px">Lorem Ipsum is simply dummy unknown printer took a galley of type and scrambled it to make.</div>
  <div class="qa-box" style="left:291px;top:87px;background:var(--red)">A</div><div class="qa-text" style="left:323px;top:88px">type and scrambled it to make. Lorem Ipsum is simply dummy unknown printer took a galley of</div>
  <div class="qa-box" style="left:291px;top:128px;background:var(--red)">A</div><div class="qa-text" style="left:323px;top:129px">Lorem Ipsum is simply dummy unknown printer took a galley of type and scrambled it to make.</div>
  <div class="qa-box" style="left:291px;top:169px;background:var(--red)">A</div><div class="qa-text" style="left:323px;top:170px">Lorem Ipsum is simply dummy unknown printer took a galley of type and scrambled it to make.</div>
  <div class="qa-box" style="left:291px;top:210px;background:var(--red)">A</div><div class="qa-text" style="left:323px;top:211px">Lorem Ipsum is simply dummy unknown printer took a galley of type and scrambled it to make.</div>
 </div>
</div>

<div class="cell" style="left:268px;top:1049px">
 <div class="slide" style="background:linear-gradient(135deg,#ffffff,#f1f2f5)">
  <div class="abs brandmark" style="left:72px;top:36px;font-size:16px;color:var(--red)">Ledger Lanternfox</div>
  <div class="abs" style="left:70px;top:82px;width:136px;height:32px;background:var(--blue);display:flex;align-items:center;gap:10px;padding-left:12px;color:#fff;font-size:5.5px"><svg width="10" height="10"><circle cx="5" cy="5" r="4" fill="none" stroke="#fff"/><line x1="1" y1="5" x2="9" y2="5" stroke="#fff"/><ellipse cx="5" cy="5" rx="1.8" ry="4" fill="none" stroke="#fff"/></svg>www.ledgerlanternfox.example</div>
  <div class="abs" style="left:70px;top:118px;width:136px;height:32px;background:#fff;box-shadow:0 1px 4px rgba(0,0,0,.1);display:flex;align-items:center;gap:10px;padding-left:12px;color:var(--muted);font-size:5px;line-height:1.3"><svg width="10" height="12"><path d="M5 11 C1 6 1 4 1 4 a4 4 0 0 1 8 0 c0 0 0 2 -4 7z" fill="none" stroke="var(--blue)"/><circle cx="5" cy="4" r="1.5" fill="var(--blue)"/></svg><span>Here to write your<br>Company adress</span></div>
  <div class="abs" style="left:70px;top:154px;width:136px;height:32px;background:#fff;box-shadow:0 1px 4px rgba(0,0,0,.1);display:flex;align-items:center;gap:10px;padding-left:12px;color:var(--muted);font-size:5px"><svg width="10" height="10"><path d="M2 1 l2 0 l1 3 l-1.5 1 a6 6 0 0 0 2.5 2.5 l1 -1.5 l3 1 l0 2 a1 1 0 0 1 -1 1 a9 9 0 0 1 -8 -8 a1 1 0 0 1 1 -1z" fill="var(--blue)"/></svg>(555) 010-0199</div>
  <div class="abs" style="left:70px;top:190px;width:136px;height:32px;background:#fff;box-shadow:0 1px 4px rgba(0,0,0,.1);display:flex;align-items:center;gap:10px;padding-left:12px;color:var(--muted);font-size:5px"><svg width="11" height="8"><rect x=".5" y=".5" width="10" height="7" fill="var(--blue)"/><path d="M.5 .5 l5 4 l5 -4" fill="none" stroke="#fff" stroke-width=".8"/></svg>hello@ledgerlanternfox.example</div>
  <div class="abs" style="left:102px;top:232px;display:flex;gap:4px"><span style="width:9px;height:9px;background:var(--blue);border-radius:2px"></span><span style="width:9px;height:9px;background:var(--blue);border-radius:2px"></span><span style="width:9px;height:9px;background:var(--blue);border-radius:2px"></span><span style="width:9px;height:9px;background:var(--blue);border-radius:2px"></span></div>
  <div class="abs heading" style="left:265px;top:128px;font-size:31px;font-weight:600;color:#1f3764">THANK YOU</div>
 </div>
</div>

<div class="cell" style="left:528px;top:1049px">
 <div class="slide">
  <div class="rail"><span class="dot"></span><span class="brand">Ledger Lanternfox</span><span class="num">24</span></div>
  <svg class="abs" style="left:0;top:0" width="506" height="284" fill="none" stroke-width="1.8">
   <defs><filter id="bubbleShadow" x="-10%" y="-10%" width="120%" height="130%"><feDropShadow dx="0" dy="3" stdDeviation="4" flood-opacity=".18"/></filter></defs>
   <polyline points="183,52 117,56 135,210" stroke="var(--blue)"/>
   <polyline points="188,60 125,64 142,203" stroke="var(--red)"/>
   <polyline points="243,60 390,52 370,220" stroke="var(--blue)"/>
   <polyline points="243,68 382,60 362,212" stroke="var(--red)"/>
   <polygon points="130,86 370,78 355,210 210,212 180,245 185,212 140,212" fill="#fff" stroke="none" filter="url(#bubbleShadow)"/>
   <polyline points="160,215 180,250 198,215" stroke="var(--blue)"/>
   <polyline points="170,215 184,240 192,215" stroke="var(--red)"/>
  </svg>
  <div class="abs heading center" style="left:130px;width:240px;top:128px;font-size:29px;color:#1f3764">Questions?</div>
 </div>
</div>

</body>
</html>
```